Website update for Harborline Ledger Partners & Bookkeeping

Our website needs updating
www.harborlineledgerpartners.com
Here are some of our latest print pieces to use as a guide?
I have also attached our graphic identity guide which includes the Pantone colors

Target Market(s)

Insurance Agencies

Industry/Entity Type

Accounting

Number of Pages Required

5+ page

```html
<!DOCTYPE html>
<html lang="en">
<head>
<meta charset="utf-8">
<title>Harborline Ledger Partners &amp; Bookkeeping</title>
<link href="https://fonts.googleapis.com/css2?family=Open+Sans:wght@400;600;700;800&display=swap" rel="stylesheet">
<style>
:root{
  --teal:#16a89a;
  --teal-dark:#0f8a7e;
  --lime:#b5c827;
  --ink:#333b3f;
  --muted:#6d7478;
  --light:#f1f3f3;
  --line:#dfe3e3;
  --white:#ffffff;
}
*{margin:0;padding:0;box-sizing:border-box}
html,body{width:1200px;height:2400px;overflow:hidden}
body{font-family:"Open Sans",Arial,sans-serif;color:var(--ink);background:var(--white);position:relative}
.page{width:1200px;height:2400px;position:relative}

/* header */
.site-header{position:absolute;left:0;top:0;width:1200px;height:130px}
.brand{position:absolute;left:60px;top:24px;display:flex;align-items:center;gap:10px}
.brand-square{width:34px;height:34px;background:var(--teal);flex:none}
.brand-name{font-weight:700;font-size:15px;color:var(--teal);line-height:1.2;width:200px}
.tagline{position:absolute;left:420px;top:20px;width:360px;text-align:center;font-size:14px;color:var(--muted);line-height:1.5}
.header-actions{position:absolute;right:60px;top:18px;display:flex;gap:22px;align-items:center}
.btn-join{background:var(--teal);color:var(--white);font-size:14px;font-weight:600;padding:9px 24px;border-radius:3px}
.link-contact{font-size:14px;color:var(--teal);font-weight:600}
.main-nav{position:absolute;right:60px;top:88px;display:flex;gap:26px;font-size:12px;font-weight:600;color:var(--ink);letter-spacing:.4px}
.main-nav span:first-child{color:var(--teal)}

/* hero */
.hero{position:absolute;left:0;top:130px;width:1200px;height:620px;background:linear-gradient(120deg,#f4f5f5 0%,#e5e8e9 45%,#cfd4d6 100%)}
.hero-copy{position:absolute;right:120px;top:450px;text-align:right}
.hero-line1{display:inline-block;background:var(--teal);color:var(--white);font-size:26px;font-weight:700;padding:10px 22px}
.hero-line2{display:inline-block;background:var(--white);color:var(--ink);font-size:26px;font-weight:700;padding:10px 22px;margin-top:8px}
.hero-dots{position:absolute;left:0;width:1200px;top:766px;display:flex;justify-content:center;gap:8px}
.hero-dots i{width:8px;height:8px;border-radius:50%;background:var(--line)}
.hero-dots i:first-child{background:var(--teal)}

/* welcome */
.welcome{position:absolute;top:800px;left:0;width:1200px;text-align:center}
.section-title{font-size:30px;font-weight:800;letter-spacing:1px;color:var(--ink)}
.welcome-sub{font-size:16px;font-weight:700;margin-top:10px;color:var(--ink)}
.welcome-text{width:980px;margin:14px auto 0;font-size:12px;line-height:1.75;color:var(--muted)}
.features{display:flex;justify-content:center;gap:160px;margin-top:28px}
.feature{width:160px;text-align:center}
.feature svg{width:64px;height:64px}
.feature p{font-size:14px;margin-top:6px;color:var(--ink);line-height:1.3}

/* about */
.about{position:absolute;top:1140px;left:0;width:1200px;height:310px;background:var(--teal)}
.about-photo{position:absolute;left:140px;top:55px;width:150px;height:200px;background:linear-gradient(160deg,#d8cfc7,#8a7a70);border:4px solid var(--white)}
.about-body{position:absolute;left:330px;top:56px;width:720px;color:var(--white)}
.about-body h2{font-size:30px;font-weight:800;letter-spacing:1px}
.about-body p{font-size:12px;line-height:1.75;margin-top:10px;color:#e6f6f4}
.btn-more{display:inline-block;margin-top:18px;background:var(--lime);color:var(--white);font-size:11px;font-weight:700;padding:9px 20px;border-radius:2px}

/* services */
.services{position:absolute;top:1520px;left:0;width:1200px;text-align:center}
.service-grid{display:flex;justify-content:center;gap:34px;margin-top:40px}
.service{width:110px}
.service .dot{width:80px;height:80px;border-radius:50%;background:var(--teal);margin:0 auto;display:flex;align-items:center;justify-content:center}
.service .dot svg{width:38px;height:38px}
.service p{font-size:10.5px;font-weight:700;color:var(--teal);margin-top:12px;line-height:1.4;text-transform:uppercase}

/* footer */
.site-footer{position:absolute;top:1860px;left:0;width:1200px;height:540px;background:var(--light);border-top:1px solid var(--line)}
.footer-col{position:absolute;top:44px}
.footer-brand{left:120px;width:360px}
.footer-brand .brand{position:static}
.footer-brand h4{font-size:13px;font-weight:600;margin-top:26px;color:var(--ink)}
.subscribe{display:flex;margin-top:12px}
.subscribe .field{width:220px;height:34px;border:1px solid var(--line);background:var(--white);font-size:11px;color:#a3a8aa;padding:9px 10px}
.subscribe .send{height:34px;background:var(--teal);color:var(--white);font-size:11px;font-weight:700;padding:10px 16px}
.socials{display:flex;gap:10px;margin-top:16px}
.socials i{width:20px;height:20px;border-radius:50%;background:var(--teal)}
.footer-nav{left:620px;width:200px}
.footer-col h3{font-size:16px;font-weight:700;color:var(--ink);margin-bottom:14px}
.footer-nav li{list-style:none;font-size:12px;color:var(--muted);padding:6px 0}
.footer-contact{left:860px;width:260px}
.contact-row{display:flex;gap:8px;font-size:12px;color:var(--muted);line-height:1.6;margin-bottom:8px}
.contact-row svg{width:14px;height:14px;flex:none;margin-top:3px}
.copyright{position:absolute;bottom:0;left:0;width:1200px;height:50px;border-top:1px solid var(--line);background:var(--white);text-align:center;font-size:10px;line-height:50px;color:var(--muted);letter-spacing:.5px}
</style>
</head>
<body>
<div class="page">

<header class="site-header">
  <div class="brand"><span class="brand-square"></span><span class="brand-name">Harborline Ledger Partners &amp; Bookkeeping</span></div>
  <p class="tagline">Specialists in providing accounting support services to Independent Insurance Agencies</p>
  <div class="header-actions"><span class="btn-join">Join Now</span><span class="link-contact">Contact Us</span></div>
  <nav class="main-nav"><span>HOME</span><span>ABOUT US</span><span>CHARGES</span><span>OUR SERVICES</span><span>HOW IT WORKS</span><span>RESOURCES</span><span>CONTACT US</span><span>BLOG</span></nav>
</header>

<section class="hero" role="img" aria-label="Desk scene with calculator, pen and financial papers">
  <div class="hero-copy">
    <div><span class="hero-line1">Need help with your insurance agency's</span></div>
    <div><span class="hero-line2">accounting and bookkeeping?</span></div>
  </div>
</section>
<div class="hero-dots"><i></i><i></i><i></i><i></i></div>

<section class="welcome">
  <h2 class="section-title">WELCOME</h2>
  <p class="welcome-sub">Experienced team of insurance agency bookkeeping professionals maintaining your books</p>
  <p class="welcome-text">Harborline Ledger Partners is an accounting practice with many years of experience in bookkeeping, reconciliation and financial reporting for independent insurance agencies. We bring a proven track record of improving efficiency in agency bookkeeping and implementing technology solutions across agencies of every size. Our team understands the commission cycle, direct bill and agency bill processes, and the reports your carriers expect. Whether you run a small office or a multi-location agency, we keep your books current, accurate and ready for review, so you can focus on your clients and growth.</p>
  <div class="features">
    <div class="feature">
      <svg viewBox="0 0 70 70" fill="none" stroke="var(--teal)" stroke-width="3"><rect x="18" y="10" width="34" height="50" rx="3"/><path d="M26 24h18M26 33h18M26 42h12"/></svg>
      <p>Bookkeeping tasks</p>
    </div>
    <div class="feature">
      <svg viewBox="0 0 70 70" fill="none" stroke="var(--teal)" stroke-width="3"><rect x="14" y="14" width="42" height="42" rx="3"/><path d="M22 46V36M32 46V28M42 46V22"/></svg>
      <p>Financial statements prepared</p>
    </div>
    <div class="feature">
      <svg viewBox="0 0 70 70" fill="none" stroke="var(--teal)" stroke-width="3"><circle cx="35" cy="35" r="24"/><path d="M25 35l7 7 14-15"/></svg>
      <p>Sample of special projects</p>
    </div>
  </div>
</section>

<section class="about">
  <div class="about-photo" role="img" aria-label="Portrait of the practice founder"></div>
  <div class="about-body">
    <h2>ABOUT US</h2>
    <p>Dana Whitcomb is an accounting professional with many years of experience in bookkeeping and financial reporting for independent insurance agencies. She has a proven record of improving efficiency in agency accounting and putting technology solutions in place across the region. Dana founded Harborline Ledger Partners to give agencies a dependable, specialised partner. Whether your agency needs a part-time bookkeeper or a full review of its accounts, our team builds a plan that suits your size, workflow and budget.</p>
    <span class="btn-more">READ MORE</span>
  </div>
</section>

<section class="services">
  <h2 class="section-title">SERVICES AVAILABLE</h2>
  <div class="service-grid">
    <div class="service"><div class="dot"><svg viewBox="0 0 38 38" fill="none" stroke="#fff" stroke-width="2.5"><rect x="6" y="10" width="26" height="18" rx="2"/><circle cx="19" cy="19" r="4"/></svg></div><p>Process payroll</p></div>
    <div class="service"><div class="dot"><svg viewBox="0 0 38 38" fill="none" stroke="#fff" stroke-width="2.5"><rect x="9" y="5" width="20" height="28" rx="2"/><path d="M14 13h10M14 19h10M14 25h6"/></svg></div><p>Pay carrier invoices</p></div>
    <div class="service"><div class="dot"><svg viewBox="0 0 38 38" fill="none" stroke="#fff" stroke-width="2.5"><circle cx="19" cy="14" r="6"/><path d="M8 32c2-7 20-7 22 0"/></svg></div><p>Reconcile customer accounts receivable</p></div>
    <div class="service"><div class="dot"><svg viewBox="0 0 38 38" fill="none" stroke="#fff" stroke-width="2.5"><path d="M6 10h26M6 19h26M6 28h26"/></svg></div><p>Reconcile general ledger accounts</p></div>
    <div class="service"><div class="dot"><svg viewBox="0 0 38 38" fill="none" stroke="#fff" stroke-width="2.5"><path d="M8 30V20M16 30V13M24 30V17M32 30V8"/></svg></div><p>Prepare &amp; interpret financial statements</p></div>
    <div class="service"><div class="dot"><svg viewBox="0 0 38 38" fill="none" stroke="#fff" stroke-width="2.5"><circle cx="17" cy="17" r="9"/><path d="M24 24l8 8"/></svg></div><p>Review direct bill commission</p></div>
    <div class="service"><div class="dot"><svg viewBox="0 0 38 38" fill="none" stroke="#fff" stroke-width="2.5"><circle cx="19" cy="19" r="13"/><path d="M13 19l4 4 8-9"/></svg></div><p>Reconcile &amp; pay agency bill premiums</p></div>
  </div>
</section>

<footer class="site-footer">
  <div class="footer-col footer-brand">
    <div class="brand"><span class="brand-square"></span><span class="brand-name">Harborline Ledger Partners &amp; Bookkeeping</span></div>
    <h4>Subscribe to our newsletter</h4>
    <div class="subscribe"><span class="field">Your email</span><span class="send">SUBSCRIBE</span></div>
    <div class="socials"><i></i><i></i><i></i><i></i><i></i></div>
  </div>
  <div class="footer-col footer-nav">
    <h3>Site Map</h3>
    <ul><li>Home</li><li>About Us</li><li>Charges</li><li>Our Services</li><li>How It Works</li><li>Resources</li><li>Contact Us</li><li>Blog</li></ul>
  </div>
  <div class="footer-col footer-contact">
    <h3>Contact</h3>
    <div class="contact-row"><svg viewBox="0 0 14 14" fill="var(--teal)"><path d="M7 0a5 5 0 0 0-5 5c0 4 5 9 5 9s5-5 5-9a5 5 0 0 0-5-5zm0 7a2 2 0 1 1 0-4 2 2 0 0 1 0 4z"/></svg><span>Harborline Ledger Partners &amp; Bookkeeping<br>418 Quayside Lane<br>Port Alder, ME 04110</span></div>
    <div class="contact-row"><svg viewBox="0 0 14 14" fill="var(--teal)"><path d="M3 1l2 3-1.5 1.5a8 8 0 0 0 5 5L10 9l3 2-1 2.5C6 13 1 8 .5 2z"/></svg><span>Tel: (207) 555-0148</span></div>
    <div class="contact-row"><svg viewBox="0 0 14 14" fill="var(--teal)"><rect x="1" y="4" width="12" height="8" rx="1"/><rect x="4" y="1" width="6" height="3"/></svg><span>Fax: (207) 555-0149</span></div>
    <div class="contact-row"><svg viewBox="0 0 14 14" fill="none" stroke="var(--teal)" stroke-width="1.5"><rect x="1" y="3" width="12" height="9"/><path d="M1 3l6 5 6-5"/></svg><span>hello@harborlineledgerpartners.com</span></div>
  </div>
  <div class="copyright">© 2015 HARBORLINE. ALL RIGHTS RESERVED</div>
</footer>

</div>
</body>
</html>
```